Oil and Gas Exploration and Production company needs a business card design

We need a business card design using our logo and colors in the logo. We want a mainstream design.

```html
<!DOCTYPE html>
<html lang="en">
<head>
<meta charset="utf-8">
<title>Kestrel Oil &amp; Gas – Business Card</title>
<link rel="stylesheet" href="https://fonts.googleapis.com/css2?family=Arimo:wght@400;700&display=swap">
<style>
  :root {
    --page-bg: #e9e6e1;
    --card-bg: #f4f3f1;
    --card-edge: #d6d3ce;
    --ink-dark: #231f20;
    --ink-text: #2b2b2b;
    --gold: #c08a2a;
    --gold-light: #d6a443;
  }
  * { box-sizing: border-box; margin: 0; padding: 0; }
  html, body {
    width: 1200px; height: 970px; overflow: hidden;
    background: var(--page-bg);
    font-family: "Arimo", Arial, sans-serif;
  }
  .card {
    position: absolute; left: 100px; top: 185px;
    width: 1000px; height: 601px;
    background: var(--card-bg);
    border: 1px solid var(--card-edge);
    overflow: hidden;
    box-shadow: 0 10px 30px rgba(0,0,0,.12);
  }
  .brand {
    position: absolute; left: 50px; top: 72px;
    display: flex; align-items: center; gap: 16px;
  }
  .brand-dot {
    width: 40px; height: 40px; border-radius: 50%;
    background: var(--gold);
  }
  .brand-name {
    font-weight: 700; font-size: 58px; line-height: 1;
    color: var(--ink-dark); letter-spacing: -1px;
  }
  .info-group {
    position: absolute; left: 40px;
    border-left: 6px solid var(--ink-dark);
    padding-left: 26px;
  }
  .info-group.gold-bar { border-left-color: var(--gold); }
  .person { top: 282px; }
  .person-name { font-size: 31px; font-weight: 700; color: var(--gold); line-height: 1.15; }
  .person-title { font-size: 23px; color: var(--ink-text); line-height: 1.3; }
  .address { top: 382px; font-size: 20px; line-height: 1.4; color: var(--gold); }
  .contacts { top: 472px; font-size: 23px; color: var(--ink-text); }
  .contact-line { display: flex; align-items: center; gap: 12px; height: 36px; }
  .contact-line.web { color: var(--gold); font-weight: 700; font-size: 21px; }
  .contact-icon { width: 22px; height: 22px; flex: none; }
  .accent-disc {
    position: absolute; left: 610px; top: 195px;
    width: 400px; height: 400px; border-radius: 50%;
    background: var(--ink-dark);
  }
</style>
</head>
<body>
  <div class="card">
    <div class="brand">
      <span class="brand-dot"></span>
      <span class="brand-name">Kestrel Oil &amp; Gas</span>
    </div>

    <div class="info-group person">
      <div class="person-name">Arne Lindqvist</div>
      <div class="person-title">Director of Sales &amp; Marketing</div>
    </div>

    <div class="info-group gold-bar address">
      <div>Carden Row Ashworth</div>
      <div>Leeds LS9 4QT</div>
    </div>

    <div class="info-group contacts">
      <div class="contact-line">
        <svg class="contact-icon" viewBox="0 0 22 22" aria-hidden="true">
          <circle cx="11" cy="11" r="11" fill="var(--gold)"/>
          <path d="M6 9c1-3 9-3 10 0l-2 1-1-2H9l-1 2z M7 11h8v4H7z" fill="#fff"/>
        </svg>
        <span>555 210 4836</span>
      </div>
      <div class="contact-line">
        <svg class="contact-icon" viewBox="0 0 22 22" aria-hidden="true">
          <circle cx="11" cy="11" r="11" fill="var(--gold)"/>
          <rect x="7.5" y="5" width="7" height="12" rx="1.5" fill="#fff"/>
          <rect x="9" y="7" width="4" height="7" fill="var(--gold)"/>
        </svg>
        <span>arne@kestreloilgas.com</span>
      </div>
      <div class="contact-line web">
        <svg class="contact-icon" viewBox="0 0 22 22" aria-hidden="true">
          <circle cx="11" cy="11" r="11" fill="var(--gold)"/>
          <rect x="5.5" y="7" width="11" height="8" fill="#fff"/>
          <path d="M5.5 7l5.5 4.5L16.5 7" fill="none" stroke="var(--gold)" stroke-width="1.2"/>
        </svg>
        <span>www.kestreloilgas.co.uk</span>
      </div>
    </div>

    <div class="accent-disc" aria-hidden="true"></div>
  </div>
</body>
</html>
```